Business Card Design Project

We are rebranding an existing automotive collision repair business. The business is called dent haven. I have attached logo but I'm not tied to that. I want to leave this wide open.

I want this card to say we are professional, competent, cutting edge. We are focused on customers and use a lot of the latest technology to make the customer experience different. We sign customers in on iPads. Paperwork I signed electronically and updates are sent via text, email, logging on a website or as they wish. I want this innovation and image to come through in our cards

Target Market(s)

60%. Women 40% men. Age 35-60

Industry/Entity Type

Automotive

Requirements
Must have
• The card must have name, title, phone,email, cell, web page

```html
<!DOCTYPE html>
<html lang="en">
<head>
<meta charset="utf-8">
<title>Dent Haven — Business Card</title>
<link href="https://fonts.googleapis.com/css2?family=Source+Sans+3:wght@400;600;700&display=swap" rel="stylesheet">
<style>
  :root {
    --page-bg: #d9dadb;
    --card-white: #eeefef;
    --brand-green: #7ab63a;
    --green-light: #a9cf78;
    --text-white: #ffffff;
    --text-soft: #e4f0d6;
    --shadow: rgba(0, 0, 0, 0.18);
  }
  * { box-sizing: border-box; margin: 0; padding: 0; }
  html, body { width: 883px; height: 1200px; overflow: hidden; }
  body {
    background: var(--page-bg);
    font-family: "Source Sans 3", "Myriad Pro", Arial, sans-serif;
    display: flex;
    flex-direction: column;
    align-items: center;
    justify-content: center;
    gap: 80px;
  }
  .card {
    position: relative;
    width: 700px;
    height: 400px;
    background: var(--card-white);
    box-shadow: 0 6px 18px var(--shadow);
    overflow: hidden;
  }
  /* Front */
  .card-front {
    display: flex;
    flex-direction: column;
    align-items: center;
    justify-content: center;
    gap: 26px;
  }
  .brand-name {
    font-weight: 700;
    color: var(--brand-green);
    font-size: 72px;
    letter-spacing: -1px;
    line-height: 1;
  }
  .front-web {
    color: var(--brand-green);
    font-weight: 600;
    font-size: 26px;
  }
  /* Back */
  .back-wave { position: absolute; inset: 0; width: 100%; height: 100%; }
  .back-brand {
    position: absolute;
    right: 60px;
    top: 48px;
    font-size: 52px;
  }
  .holder {
    position: absolute;
    left: 42px;
    top: 208px;
    color: var(--text-white);
  }
  .holder-name { font-size: 27px; font-weight: 600; }
  .holder-title { font-size: 20px; color: var(--text-soft); margin-top: 2px; }
  .contact-list {
    position: absolute;
    left: 350px;
    top: 212px;
    list-style: none;
    color: var(--text-white);
    font-size: 21px;
  }
  .contact-list li {
    display: flex;
    align-items: center;
    gap: 9px;
    height: 30px;
  }
  .contact-list svg { width: 15px; height: 15px; fill: var(--text-white); flex: none; }
</style>
</head>
<body>

  <section class="card card-front" aria-label="Card front">
    <div class="brand-name">Dent Haven</div>
    <div class="front-web">www.denthaven.com</div>
  </section>

  <section class="card card-back" aria-label="Card back">
    <svg class="back-wave" viewBox="0 0 700 400" preserveAspectRatio="none" aria-hidden="true">
      <path d="M0,62 C140,30 260,48 400,105 S600,172 700,150 L700,400 L0,400 Z" fill="var(--green-light)"/>
      <path d="M0,78 C140,46 260,64 400,122 S600,190 700,168 L700,400 L0,400 Z" fill="var(--brand-green)"/>
    </svg>

    <div class="brand-name back-brand">Dent Haven</div>

    <div class="holder">
      <div class="holder-name">Laura Bennett</div>
      <div class="holder-title">Managing Director</div>
    </div>

    <ul class="contact-list">
      <li>
        <svg viewBox="0 0 16 16" aria-label="Phone"><path d="M3.6 1.5l2.2 2.6-1.3 1.6c.9 2 2.4 3.5 4.3 4.4l1.6-1.3 2.6 2.2-1.2 2.6C6.9 13.4 2.6 9.1 1.2 2.8z"/></svg>
        555.0142.7310
      </li>
      <li>
        <svg viewBox="0 0 16 16" aria-label="Mobile"><path d="M4.5 1h7v14h-7zM6 2.5v9.5h4V2.5zM7.3 13h1.4v1H7.3z" fill-rule="evenodd"/></svg>
        555.0142.7311
      </li>
      <li>
        <svg viewBox="0 0 16 16" aria-label="Fax"><path d="M4 1h6l2 2v3H4zM2 7h12v6h-2v2H4v-2H2zM5.5 10.5v3h5v-3z" fill-rule="evenodd"/></svg>
        555.0142.7312
      </li>
      <li>
        <svg viewBox="0 0 16 16" aria-label="Email"><path d="M1 4h14v9H1zM2.5 5.2L8 9l5.5-3.8v-.2h-11z" fill-rule="evenodd"/></svg>
        info@denthaven.com
      </li>
      <li>
        <svg viewBox="0 0 16 16" aria-label="Website"><path d="M8 1a7 7 0 1 0 0 14A7 7 0 0 0 8 1zm0 1.5c.9 1 1.5 2.7 1.6 4.5H6.4C6.5 5.2 7.1 3.5 8 2.5zM2.6 7h2.3c.1-1.6.5-3 1.1-4A5.6 5.6 0 0 0 2.6 7zm0 1.5A5.6 5.6 0 0 0 6 13c-.6-1-1-2.4-1.1-4.5zm3.8 0h3.2c-.1 1.8-.7 3.5-1.6 4.5-.9-1-1.5-2.7-1.6-4.5zm4.7 0c-.1 2.1-.5 3.5-1.1 4.5a5.6 5.6 0 0 0 3.4-4.5zM13.4 7A5.6 5.6 0 0 0 10 3c.6 1 1 2.4 1.1 4z" fill-rule="evenodd"/></svg>
        www.denthaven.com
      </li>
    </ul>
  </section>

</body>
</html>
```